A specialised Sport management needs a corporate brochure design

We are a specialized company in the management and consultancy of sports events. and need to have a company brochure
We provide the following services;
Event management
Venues management
Production
Ticketing
Consulting
Hospitality
Activity management
Event timing
Branding of event
Event supplies
We need a corporate profile design for our company to showcase the major events that we have covered , with images, information, statistics, surveys, products and services used. We want to highlight our professionalism and execution of the events, experience of the participants, spectators . How we have grown in the past few years and reached the international standards.
Objectives of the work:
To get sponsors and partners for future business and to present Tri-Crest
as not just a sports management company but also a professional sports
events management company.
You can check our website
www.tri-crest.example
Target Market(s)
Sponsors and corporate partners
Industry/Entity Type
Events
Requirements
Must have
- Must Have:
- - Very professional look
- -Some event images,Event information, statistics, surveys, products and services used. We want to highlight our professionalism and execution of the events (Attached)
Nice to have
- Similar momentom of the below design
- http://www.lumavent.example/wp-content/themes/lumavent/pdf/CP-2014-15-V10-Web.pdf

```html
<!DOCTYPE html>
<html lang="en">
<head>
<meta charset="utf-8">
<title>Tri-Crest Corporate Brochure – Covers</title>
<link href="https://fonts.googleapis.com/css2?family=Montserrat:wght@500;600&family=Questrial&display=swap" rel="stylesheet">
<style>
  :root {
    --backdrop: #e6e6e6;
    --charcoal: #2c2e31;
    --charcoal-light: #3a3d41;
    --charcoal-deep: #1f2123;
    --orange: #f05a1a;
    --orange-deep: #c9430c;
    --steel: #8c9298;
    --text-light: #e9eaeb;
    --text-muted: #c3c6c9;
    --photo-top: #6f7c6a;
    --photo-mid: #b9bfc9;
    --photo-low: #d84e4e;
  }
  * { box-sizing: border-box; margin: 0; padding: 0; }
  html, body {
    width: 1200px; height: 683px; overflow: hidden;
    background: var(--backdrop);
    font-family: "Questrial", sans-serif;
  }
  .spread {
    position: absolute; left: 140px; top: 16px;
    width: 920px; height: 650px;
    display: flex;
    box-shadow: 0 10px 30px rgba(0,0,0,.25);
  }
  .cover { position: relative; width: 460px; height: 650px; overflow: hidden; }

  /* Back cover */
  .back-cover { background: var(--charcoal); }
  .back-cover .panel {
    position: absolute; left: 170px; top: 60px; width: 290px; height: 470px;
    background: var(--charcoal-light); opacity: .7;
  }
  .swoosh { position: absolute; left: 0; width: 460px; z-index: 1; }
  .contact {
    position: absolute; right: 34px; top: 330px; z-index: 2;
    color: var(--text-light); text-align: right; white-space: nowrap;
  }
  .contact-title {
    font-family: "Montserrat", sans-serif; font-weight: 600;
    font-size: 26px; margin-bottom: 10px;
  }
  .contact-line { font-size: 15px; line-height: 21px; color: var(--text-muted); }

  /* Front cover */
  .front-cover { background: var(--charcoal-deep); }
  .event-photo {
    position: absolute; left: 0; top: 0; width: 460px; height: 650px;
    background: linear-gradient(170deg, var(--photo-top) 0%, var(--photo-mid) 40%, #9aa4b3 65%, var(--photo-low) 100%);
  }
  .brand {
    position: absolute; left: 130px; top: 70px; z-index: 2;
    display: flex; align-items: center; gap: 10px;
  }
  .brand-name {
    font-family: "Montserrat", sans-serif; font-weight: 600;
    font-size: 26px; color: var(--charcoal);
  }
  .brand-mark {
    width: 34px; height: 34px; border-radius: 50%;
    background: var(--orange);
  }
</style>
</head>
<body>
  <main class="spread">
    <section class="cover back-cover">
      <div class="panel"></div>
      <svg class="swoosh" style="top:0" width="460" height="140" viewBox="0 0 460 140">
        <path d="M0 0 H460 V40 C330 60 160 100 0 140 Z" fill="var(--charcoal-deep)"/>
        <path d="M0 118 C150 80 320 45 460 25 V40 C320 62 160 100 0 132 Z" fill="var(--steel)"/>
        <path d="M120 100 C240 70 360 45 460 30 V48 C350 62 240 85 140 104 Z" fill="var(--orange)"/>
      </svg>
      <div class="contact">
        <h2 class="contact-title">Contact Us</h2>
        <p class="contact-line">Mob: 965 5550 1234</p>
        <p class="contact-line">Tel: 965 5550 7788</p>
        <p class="contact-line">Email: events@tri-crest.example</p>
        <p class="contact-line">Website: www.tri-crest.example</p>
      </div>
      <svg class="swoosh" style="top:470px" width="460" height="180" viewBox="0 0 460 180">
        <path d="M0 150 C160 110 330 60 460 20 V180 H0 Z" fill="var(--charcoal-deep)"/>
        <path d="M140 135 C260 100 370 60 460 30 V48 C370 80 260 115 160 140 Z" fill="var(--orange)"/>
        <path d="M0 160 C160 125 320 80 460 40 V52 C320 92 160 135 0 170 Z" fill="var(--steel)" opacity=".6"/>
      </svg>
    </section>

    <section class="cover front-cover">
      <div class="event-photo" role="img" aria-label="Marathon runner crossing the finish line under a sponsor arch with confetti and a race clock"></div>
      <svg class="swoosh" style="top:0" width="460" height="120" viewBox="0 0 460 120">
        <path d="M0 0 H300 C200 20 90 40 0 60 Z" fill="var(--charcoal-deep)"/>
        <path d="M0 38 C100 20 210 8 320 0 H360 C240 14 110 36 0 58 Z" fill="var(--orange)"/>
      </svg>
      <div class="brand">
        <span class="brand-mark"></span>
        <span class="brand-name">Tri-Crest</span>
      </div>
      <svg class="swoosh" style="top:480px" width="460" height="170" viewBox="0 0 460 170">
        <path d="M0 110 C150 90 320 50 460 0 V170 H0 Z" fill="var(--charcoal)"/>
        <path d="M0 100 C160 82 320 42 460 0 V22 C320 66 160 105 0 122 Z" fill="var(--orange)"/>
        <path d="M0 130 C160 112 320 75 460 35 V50 C320 90 160 125 0 145 Z" fill="var(--steel)" opacity=".6"/>
      </svg>
    </section>
  </main>
</body>
</html>
```